Trabworth Business Cards

We need a business card design for Trabworth Mining.

This is a B2B company that buys and sells large machinery tires within the coal mining industry. The design should the strong, crisp and masculine. I have uploaded the company logo and rough mock-up of what the back of the card should look like. the front of the card should have the same look/feel as the back. I need editable templates for both the front and the back of the card.

Color scheme should be grey/green/black

Contact information to include on the card:
Name: Dale Pembrose
Title: Managing Director
Phone: 555-314-2069
Address: 1187 Welford #3 Dallas, TX 75290
Email: Dale@Trabworth-example.com

I am also opening a contest for letterhead design. If you submit a business card design, please also submit a letterhead design with the same look/feel. The winner of the business card design will also will the letter head and be paid for both.

Target Market(s)

Procurement men/women in the coal mining industry

Industry/Entity Type

Coal Mining

```html
<!DOCTYPE html>
<html lang="en">
<head>
<meta charset="utf-8">
<title>Trabworth Mining — Business Cards</title>
<link rel="stylesheet" href="https://fonts.googleapis.com/css2?family=Mulish:wght@400;600;800&display=swap">
<style>
  :root {
    --backdrop: #3b3b3b;
    --card-light: #f7f7f5;
    --card-dark: #262626;
    --card-dark-edge: #1e1e1e;
    --ink-dark: #4a4a4a;
    --ink-mid: #5c5c5c;
    --brand-green: #3d9a1f;
    --ink-light: #efefef;
  }
  html, body {
    margin: 0;
    padding: 0;
    width: 1200px;
    height: 1000px;
    overflow: hidden;
    background: var(--backdrop);
    font-family: "Mulish", sans-serif;
  }
  .canvas {
    position: relative;
    width: 1200px;
    height: 1000px;
  }
  .card {
    position: absolute;
    width: 532px;
    height: 303px;
    box-sizing: border-box;
    overflow: hidden;
  }
  .card--front {
    left: 190px;
    top: 172px;
    background: var(--card-light);
  }
  .card--back {
    left: 485px;
    top: 557px;
    background: linear-gradient(135deg, var(--card-dark) 0%, var(--card-dark-edge) 100%);
  }

  /* Front */
  .brand {
    position: absolute;
    left: 32px;
    top: 130px;
    display: flex;
    align-items: center;
    gap: 10px;
  }
  .brand__square {
    width: 20px;
    height: 20px;
    background: var(--brand-green);
  }
  .brand__name {
    font-weight: 800;
    font-size: 22px;
    letter-spacing: 0.5px;
    color: var(--ink-dark);
    text-transform: uppercase;
    white-space: nowrap;
  }
  .info-block {
    position: absolute;
    left: 338px;
    border-left: 2px solid var(--brand-green);
    padding-left: 23px;
  }
  .info-block--identity {
    top: 38px;
    height: 62px;
    box-sizing: border-box;
    padding-top: 12px;
  }
  .person__name {
    margin: 0;
    font-weight: 800;
    font-size: 14px;
    letter-spacing: 0.4px;
    color: var(--ink-dark);
    text-transform: uppercase;
  }
  .person__title {
    margin: 2px 0 0;
    font-size: 12px;
    color: var(--ink-mid);
  }
  .info-block--contact {
    top: 201px;
    height: 64px;
    box-sizing: border-box;
  }
  .contact {
    margin: 0;
    font-style: normal;
    font-size: 11px;
    line-height: 15px;
    color: var(--ink-mid);
    white-space: nowrap;
  }
  .contact__label {
    font-weight: 800;
    color: var(--brand-green);
  }

  /* Back */
  .back-brand {
    position: absolute;
    right: 38px;
    top: 124px;
    display: flex;
    align-items: center;
    gap: 12px;
  }
  .back-brand__square {
    width: 22px;
    height: 22px;
    background: var(--brand-green);
  }
  .back-brand__name {
    margin: 0;
    font-weight: 800;
    font-size: 28px;
    letter-spacing: 0.5px;
    color: var(--ink-light);
    text-transform: uppercase;
    white-space: nowrap;
  }
</style>
</head>
<body>
<main class="canvas">
  <section class="card card--front" aria-label="Business card front">
    <div class="brand">
      <span class="brand__square"></span>
      <span class="brand__name">Trabworth Mining</span>
    </div>

    <div class="info-block info-block--identity">
      <h1 class="person__name">Dale Pembrose</h1>
      <p class="person__title">Managing Director</p>
    </div>

    <div class="info-block info-block--contact">
      <address class="contact">
        1187 Welford #3<br>
        Dallas, TX 75290<br>
        <span class="contact__label">T:</span> 555-314-2069<br>
        <span class="contact__label">E:</span> dale@trabworth-example.com
      </address>
    </div>
  </section>

  <section class="card card--back" aria-label="Business card back">
    <div class="back-brand">
      <span class="back-brand__square"></span>
      <p class="back-brand__name">Trabworth Mining</p>
    </div>
  </section>
</main>
</body>
</html>
```